My Music Collection - vinyl, CD

1. I want to catalogue my vinyl record collection, because it's hard to remember all the albums (and singles) I own, and that's a problem because I sometimes double up.

2. I'd like to identify my music by a) artist b) album title c) song title

3. I'd like the option of recording the quality of the album just in case I happen to find one that is a better quality

4. I would also like the album cover image, genre, record label, track listing and production date to automatically download

Target Market(s)

There has been a huge resurgence in the vinyl record market lately, but lots of people also have a CD collection. I want this app for the over 45s who have better things to remember than which albums they have!

Requirements
Must have
• 1. Be able to list my music by a) artist b) song title

2. Ideally, i would like to work with the designer when its time to update the app in the future.

3. Be creative, if I've left something out - put it in! Have a go!
Nice to have
• 1. link to something like Melvox - so i can identify songs

2. I would also like to list my singles

I would ideally like to use this app on my Vexa, and of course my Kolbet - but, i dont want the Vexa app to look like a cropped version of the Kolbet app (is that possible)?

```html
<!DOCTYPE html>
<html lang="en">
<head>
<meta charset="utf-8">
<title>Spinlog – Albums</title>
<link href="https://fonts.googleapis.com/css2?family=Arimo:wght@400;700&display=swap" rel="stylesheet">
<style>
  :root {
    --bar-top: #3a3a3a;
    --bar-bottom: #1e1e1e;
    --row-top: #fbfbfb;
    --row-bottom: #e9e9e9;
    --row-line: #c9c9c9;
    --label: #2b2b2b;
    --value: #444;
    --meta: #7a7a7a;
    --tab-text: #bdbdbd;
    --tab-active: #ffffff;
    --icon: #9a9a9a;
    --disc: #1b1b1b;
    --title: #f2f2f2;
  }
  * { box-sizing: border-box; margin: 0; padding: 0; }
  html, body { width: 800px; height: 1200px; overflow: hidden; background: #fff; }
  body { font-family: "Arimo", "Helvetica Neue", Arial, sans-serif; position: relative; }

  .nav-bar {
    position: absolute; top: 0; left: 0; width: 800px; height: 112px;
    background: linear-gradient(var(--bar-top), var(--bar-bottom));
    border-bottom: 2px solid #111;
  }
  .app-title {
    position: absolute; left: 0; right: 0; top: 0; height: 112px;
    display: flex; align-items: center; justify-content: center;
    font-size: 40px; font-weight: 700; color: var(--title);
  }
  .nav-button {
    position: absolute; top: 22px; height: 70px;
    background: linear-gradient(#3c3c3c, #151515);
    border: 2px solid #0c0c0c; border-radius: 8px;
    box-shadow: inset 0 1px 0 rgba(255,255,255,.18);
    color: #fff; font-weight: 700; font-size: 29px;
    display: flex; align-items: center; justify-content: center;
  }
  .nav-button.back { left: 26px; width: 110px; border-radius: 4px 8px 8px 4px; }
  .nav-button.back::before {
    content: ""; position: absolute; left: -15px; top: 10px; width: 46px; height: 46px;
    background: linear-gradient(135deg, #3c3c3c, #151515);
    border-left: 2px solid #0c0c0c; border-bottom: 2px solid #0c0c0c;
    transform: rotate(45deg); border-radius: 4px; z-index: 0;
  }
  .nav-button.back span { position: relative; z-index: 1; margin-left: 4px; }
  .nav-button.add { right: 15px; width: 104px; font-size: 46px; }

  .album-list { position: absolute; top: 112px; left: 0; width: 800px; height: 944px; overflow: hidden; }
  .album-row {
    position: relative; height: 278px;
    background: linear-gradient(var(--row-top), var(--row-bottom));
    border-bottom: 2px solid var(--row-line);
  }
  .record { position: absolute; left: 50px; top: 41px; width: 225px; height: 182px; }
  .record .disc { position: absolute; left: 60px; top: 0; }
  .record .cover {
    position: absolute; left: 0; top: 0; width: 181px; height: 181px;
    border: 2px solid #555; border-radius: 3px;
    box-shadow: 0 2px 4px rgba(0,0,0,.35);
  }
  .cover.c1 { background: linear-gradient(160deg, #efe3c4, #cdbb93); }
  .cover.c2 { background: linear-gradient(135deg, #c9d9e8, #6d7f8e 55%, #d94b6c); }
  .cover.c3 { background: linear-gradient(160deg, #4b1f4c, #2b0f2e); }
  .cover.c4 { background: linear-gradient(160deg, #e8eef0, #c5d3d6); }
  .album-info { position: absolute; left: 341px; top: 47px; }
  .info-line { font-size: 24px; color: var(--label); line-height: 35px; white-space: nowrap; }
  .info-line .value { font-size: 20px; color: var(--value); }
  .track-count { margin-top: 13px; font-size: 16px; color: var(--meta); }

  .scroll-indicator {
    position: absolute; left: 775px; top: 262px; width: 8px; height: 380px;
    background: rgba(0,0,0,.18); border-radius: 4px;
  }

  .tab-bar {
    position: absolute; left: 0; top: 1056px; width: 800px; height: 144px;
    background: linear-gradient(#333, #1a1a1a); border-top: 2px solid #0d0d0d;
    display: flex;
  }
  .tab { flex: 1; position: relative; text-align: center; }
  .tab svg { position: absolute; left: 50%; top: 18px; transform: translateX(-50%); }
  .tab-label {
    position: absolute; left: 0; right: 0; top: 94px;
    font-size: 25px; font-weight: 700; color: var(--tab-text);
    text-shadow: 0 -1px 0 #000;
  }
  .tab.active .tab-label { color: var(--tab-active); }
</style>
</head>
<body>
  <header class="nav-bar">
    <div class="nav-button back"><span>Back</span></div>
    <div class="app-title">Spinlog</div>
    <div class="nav-button add">+</div>
  </header>

  <main class="album-list">
    <article class="album-row">
      <div class="record">
        <svg class="disc" width="165" height="165" viewBox="0 0 165 165" aria-hidden="true"><circle cx="82" cy="91" r="70" fill="var(--disc)"/><circle cx="82" cy="91" r="52" fill="none" stroke="#333" stroke-width="2"/></svg>
        <div class="cover c1" role="img" aria-label="Album cover artwork for Iron Mask"></div>
      </div>
      <div class="album-info">
        <p class="info-line">Album Name: <span class="value">Iron Mask</span></p>
        <p class="info-line">Artist Name: <span class="value">Halden Roe</span></p>
        <p class="info-line">Release Year: <span class="value">2005</span></p>
        <p class="track-count">15 Tracks Inside</p>
      </div>
    </article>

    <article class="album-row">
      <div class="record">
        <svg class="disc" width="165" height="165" viewBox="0 0 165 165" aria-hidden="true"><circle cx="82" cy="91" r="70" fill="var(--disc)"/><circle cx="82" cy="91" r="52" fill="none" stroke="#333" stroke-width="2"/></svg>
        <div class="cover c2" role="img" aria-label="Album cover artwork for Cold Signals"></div>
      </div>
      <div class="album-info">
        <p class="info-line">Album Name: <span class="value">Cold Signals</span></p>
        <p class="info-line">Artist Name: <span class="value">Marlo Veight</span></p>
        <p class="info-line">Release Year: <span class="value">2008</span></p>
        <p class="track-count">12 Tracks Inside</p>
      </div>
    </article>

    <article class="album-row">
      <div class="record">
        <svg class="disc" width="165" height="165" viewBox="0 0 165 165" aria-hidden="true"><circle cx="82" cy="91" r="70" fill="var(--disc)"/><circle cx="82" cy="91" r="52" fill="none" stroke="#333" stroke-width="2"/></svg>
        <div class="cover c3" role="img" aria-label="Album cover artwork for Tune In Again"></div>
      </div>
      <div class="album-info">
        <p class="info-line">Album Name: <span class="value">Tune In Again</span></p>
        <p class="info-line">Artist Name: <span class="value">Mixed by Calder</span></p>
        <p class="info-line">Release Year: <span class="value">2006</span></p>
        <p class="track-count">12 Tracks Inside</p>
      </div>
    </article>

    <article class="album-row">
      <div class="record">
        <svg class="disc" width="165" height="165" viewBox="0 0 165 165" aria-hidden="true"><circle cx="82" cy="91" r="70" fill="var(--disc)"/><circle cx="82" cy="91" r="52" fill="none" stroke="#333" stroke-width="2"/></svg>
        <div class="cover c4" role="img" aria-label="Album cover artwork"></div>
      </div>
      <div class="album-info">
        <p class="info-line">Album Name: <span class="value">Tune In Again</span></p>
        <p class="info-line">Artist Name: <span class="value">Mixed by Calder</span></p>
      </div>
    </article>
  </main>

  <div class="scroll-indicator"></div>

  <nav class="tab-bar">
    <div class="tab">
      <svg width="84" height="64" viewBox="0 0 84 64" aria-hidden="true" fill="var(--icon)">
        <circle cx="20" cy="22" r="10" opacity=".7"/><path d="M2 56c0-14 8-22 18-22s18 8 18 22z" opacity=".7"/>
        <circle cx="64" cy="22" r="10" opacity=".7"/><path d="M46 56c0-14 8-22 18-22s18 8 18 22z" opacity=".7"/>
        <circle cx="42" cy="18" r="12"/><path d="M20 60c0-17 10-26 22-26s22 9 22 26z"/>
      </svg>
      <span class="tab-label">Artist</span>
    </div>
    <div class="tab active">
      <svg width="72" height="72" viewBox="0 0 72 72" aria-hidden="true"><circle cx="36" cy="36" r="34" fill="#f4f4f4"/><circle cx="36" cy="36" r="14" fill="#2a2a2a"/><circle cx="36" cy="36" r="7" fill="#f4f4f4"/></svg>
      <span class="tab-label">Albums</span>
    </div>
    <div class="tab">
      <svg width="80" height="70" viewBox="0 0 80 70" aria-hidden="true" fill="none" stroke="var(--icon)" stroke-width="7"><path d="M12 48V36a28 28 0 0 1 56 0v12"/><rect x="6" y="40" width="14" height="26" rx="4" fill="var(--icon)" stroke="none"/><rect x="60" y="40" width="14" height="26" rx="4" fill="var(--icon)" stroke="none"/></svg>
      <span class="tab-label">Playing</span>
    </div>
    <div class="tab">
      <svg width="70" height="70" viewBox="0 0 70 70" aria-hidden="true" fill="var(--icon)"><path d="M22 10l40-8v46h-6V14l-28 6v36h-6z"/><ellipse cx="17" cy="56" rx="11" ry="9"/><ellipse cx="51" cy="48" rx="11" ry="9"/></svg>
      <span class="tab-label">Song</span>
    </div>
    <div class="tab">
      <svg width="80" height="70" viewBox="0 0 80 70" aria-hidden="true"><path d="M40 68L8 36C-2 26 2 6 20 4c9-1 16 4 20 10 4-6 11-11 20-10 18 2 22 22 12 32z" fill="var(--icon)"/></svg>
      <span class="tab-label">Wishlist</span>
    </div>
  </nav>
</body>
</html>
```